Yard sign design for high end luxury home builder.

Need a design for signage on custom homes that are being built. I already have a logo that I am satisfied with that needs to be incorporated. I need the following incorporated in the design of the sign-
- Lic number 381526
- phone number (805) 555-0148‬
- quennbuilderscrew.com
- Logo/Branding

If possible it may be nice to have the following quote that is on are business cards-

Quote from Gerard of Norvelle-
HE WHO WORKS WITH HIS HANDS IS A LABORER.
HE WHO WORKS WITH HIS HANDS & HIS HEAD IS A CRAFTSMAN.
HE WHO WORKS WITH HIS HANDS & HIS HEAD & HIS HEART IS AN ARTISAN.
-GERARD OF NORVELLE

Target Market(s)

Archetect, Designers, Clients desiring to build a new home or remodel.

Colors
fde9d4
fee4d5
fabb94
fac994
faa54b
f68d4d
f37122
f78f20
f68e4e

Requirements
Must have
• - Lic number 381526
• - phone number (805) 555-0148‬
• - quennbuilderscrew.com
• - Logo/Branding
Nice to have
• Quote from Gerard of Norvelle-
• HE WHO WORKS WITH HIS HANDS IS A LABORER.
• HE WHO WORKS WITH HIS HANDS & HIS HEAD IS A CRAFTSMAN.
• HE WHO WORKS WITH HIS HANDS & HIS HEAD & HIS HEART IS AN ARTISAN.
• -GERARD OF NORVELLE
• OR the below statement-
• Craftsmen that Care
Should not have
• Any additional verbiage not specified above including any type of verbiage about what kind of company we are. For instance- Integrity, reputable... It's just all played out. Im just looking for a bitching design that has the info that compliments my logo/branding.

```html
<!DOCTYPE html>
<html lang="en">
<head>
<meta charset="UTF-8">
<title>Quenn Builders Crew – Yard Sign</title>
<link rel="stylesheet" href="https://fonts.googleapis.com/css2?family=Montserrat:ital,wght@0,500;0,600;0,700;0,800;1,500&display=swap">
<style>
  :root {
    --canvas-bg: #e6e6e4;
    --orange-deep: #f37122;
    --orange-warm: #f78f20;
    --orange-glow: #fac994;
    --white: #ffffff;
    --panel-top: #d9d9d9;
    --panel-bottom: #ffffff;
    --brand-brown: #7a6650;
    --quote-brown: #4a3a2c;
  }
  * { margin: 0; padding: 0; box-sizing: border-box; }
  html, body {
    width: 1200px; height: 1000px; overflow: hidden;
    background: var(--canvas-bg);
    font-family: "Montserrat", Arial, sans-serif;
  }
  .yard-sign {
    position: absolute; left: 250px; top: 40px;
    width: 700px; height: 920px;
    background: linear-gradient(180deg, var(--panel-top) 30%, var(--panel-bottom) 90%);
    box-shadow: 0 6px 18px rgba(0,0,0,0.18);
    overflow: hidden;
  }
  .header-chevron { position: absolute; left: 0; top: 0; width: 700px; height: 410px; }
  .header-text { position: absolute; left: 0; top: 0; width: 100%; text-align: center; color: var(--white); }
  .headline {
    position: absolute; left: 0; width: 100%; top: 18px;
    font-size: 104px; font-weight: 700; letter-spacing: 1px; line-height: 1;
  }
  .rule {
    position: absolute; left: 175px; width: 350px; height: 2px;
    background: linear-gradient(90deg, rgba(255,255,255,0), rgba(255,255,255,0.95) 20%, rgba(255,255,255,0.95) 80%, rgba(255,255,255,0));
  }
  .rule-1 { top: 140px; }
  .rule-2 { top: 236px; }
  .rule-3 { top: 294px; }
  .phone {
    position: absolute; left: 0; width: 100%; top: 150px;
    font-size: 70px; font-weight: 700; line-height: 1;
  }
  .website {
    position: absolute; left: 0; width: 100%; top: 246px;
    font-size: 34px; font-weight: 600; line-height: 1;
  }
  .license {
    position: absolute; left: 0; width: 100%; top: 307px;
    font-size: 20px; font-weight: 600; letter-spacing: 0.5px; line-height: 1;
  }
  .brand {
    position: absolute; left: 0; top: 440px; width: 100%;
    display: flex; flex-direction: column; align-items: center;
  }
  .brand-mark { width: 240px; height: 240px; background: var(--brand-brown); }
  .brand-name {
    margin-top: 24px; text-align: center; color: var(--brand-brown);
    font-weight: 800; line-height: 1;
  }
  .brand-name .primary { display: block; font-size: 44px; letter-spacing: 3px; }
  .brand-name .secondary { display: block; font-size: 22px; letter-spacing: 2px; margin-top: 6px; }
  .quote {
    position: absolute; left: 0; top: 810px; width: 100%;
    color: var(--quote-brown); text-align: center;
    font-size: 15px; font-weight: 500; line-height: 1.3; letter-spacing: 0.2px;
  }
  .quote cite {
    display: block; text-align: right; padding-right: 36px;
    font-style: italic; font-size: 14px; margin-top: 2px;
  }
</style>
</head>
<body>
  <main class="yard-sign">
    <svg class="header-chevron" viewBox="0 0 700 410" aria-hidden="true">
      <defs>
        <linearGradient id="orangeFill" x1="0" y1="0" x2="0" y2="1">
          <stop offset="0" stop-color="#f37122"/>
          <stop offset="1" stop-color="#f78f20"/>
        </linearGradient>
        <linearGradient id="edgeGlow" x1="0" y1="0" x2="1" y2="0">
          <stop offset="0.2" stop-color="#ffffff" stop-opacity="0"/>
          <stop offset="0.5" stop-color="#ffffff" stop-opacity="0.9"/>
          <stop offset="0.8" stop-color="#ffffff" stop-opacity="0"/>
        </linearGradient>
      </defs>
      <polygon points="0,0 700,0 700,286 363,400 337,400 0,286" fill="url(#orangeFill)"/>
      <polyline points="150,342 350,398 550,342" fill="none" stroke="url(#edgeGlow)" stroke-width="3"/>
    </svg>

    <header class="header-text">
      <h1 class="headline">FOR SALE</h1>
      <div class="rule rule-1"></div>
      <p class="phone">(805) 555-0148</p>
      <div class="rule rule-2"></div>
      <p class="website">www.quennbuilderscrew.com</p>
      <div class="rule rule-3"></div>
      <p class="license">LIC NUMBER 381526</p>
    </header>

    <section class="brand">
      <div class="brand-mark" aria-hidden="true"></div>
      <p class="brand-name">
        <span class="primary">QUENN BUILDERS</span>
        <span class="secondary">CREW INC.</span>
      </p>
    </section>

    <blockquote class="quote">
      HE WHO WORKS WITH HIS HANDS IS A LABORER.<br>
      HE WHO WORKS WITH HIS HANDS &amp; HIS HEAD IS A CRAFTSMAN.<br>
      HE WHO WORKS WITH HIS HANDS &amp; HIS HEAD &amp; HIS HEART IS AN ARTISAN.
      <cite>–GERARD OF NORVELLE</cite>
    </blockquote>
  </main>
</body>
</html>
```